Brightmoor Talent company

We require a website for job recruitment company called "Brightmoor Talent"
Our company is specialising in recruitment of skilled labour from Sri Lanka into Australian market.
We would like to include a job advertising plugin where jobs can be listed and applied for .
COPYWRITING MUST BE INCLUDED !

Industry/Entity Type

Recruitment

Coding

Coded - Design and coding required

Number of Pages Required

5+ page

Colors

Designer to choose colors to be used in the design.

```html
<!DOCTYPE html>
<html lang="en">
<head>
<meta charset="utf-8">
<title>Brightmoor Talent — Skilled Sri Lankan Trades for Australia</title>
<link href="https://fonts.googleapis.com/css2?family=Poppins:wght@400;500;600;700;800&display=swap" rel="stylesheet">
<style>
:root{
  --navy:#0b3d91;
  --navy-dark:#08307a;
  --ink:#1d1d1f;
  --text:#333;
  --pale:#dcecf8;
  --grey-band:#e9ebed;
  --footer:#222325;
  --white:#fff;
  --muted:#c9c9c9;
}
*{margin:0;padding:0;box-sizing:border-box}
html,body{width:1200px;height:4812px;overflow:hidden}
body{font-family:'Poppins',sans-serif;color:var(--text);background:var(--white);position:relative}
.abs{position:absolute}
.section{position:absolute;left:0;width:1200px}
h1,h2,h3{color:var(--ink);font-weight:700}

/* header */
.site-header{top:0;height:107px;background:var(--white)}
.brand{left:75px;top:18px;font-size:30px;font-weight:700;color:var(--navy);line-height:1.1}
.brand span{display:block;font-size:20px;letter-spacing:6px;padding-left:30px;font-weight:600}
.nav{top:45px;font-size:15px;font-weight:500;color:var(--ink)}
.nav.active{color:var(--navy)}
.login{left:1019px;top:37px;width:106px;height:38px;background:var(--navy);color:#fff;border-radius:6px;font-size:15px;font-weight:600;display:flex;align-items:center;justify-content:center;gap:6px}

/* hero */
.hero{top:107px;height:641px;background:linear-gradient(90deg,#d6e9f8 0%,#e1eef8 40%,#a9b8c6 62%,#4a5870 100%)}
.hero-photo{left:560px;top:0;width:640px;height:641px;background:linear-gradient(90deg,rgba(214,233,248,0) 0%,#7c8fa8 35%,#2f4f8c 65%,#233b6f 100%)}
.hero h1{position:absolute;left:72px;top:188px;font-size:52px;line-height:1.2;color:#3a3a3c;font-weight:700}
.hero p{position:absolute;left:75px;top:324px;font-size:14.5px;line-height:28px;width:520px;color:#222}
.search{left:75px;top:403px;width:508px;height:55px;background:#fff;border:1px solid #cfd8e3;border-radius:6px}
.search span{position:absolute;left:20px;top:16px;font-size:14px;color:#333}
.search b{position:absolute;right:6px;top:6px;width:126px;height:42px;background:var(--navy);color:#fff;border-radius:6px;font-size:14px;font-weight:600;display:flex;align-items:center;justify-content:center}

/* steps */
.steps{top:748px;height:472px}
.section-title{position:absolute;left:0;width:1200px;text-align:center;font-size:33px;font-weight:700;color:var(--ink)}
.step{position:absolute;top:149px;width:240px;text-align:center}
.step .icon{width:99px;height:99px;margin:0 auto;background:var(--pale);border-radius:6px;display:flex;align-items:center;justify-content:center}
.step h3{font-size:22px;margin-top:22px;font-weight:600}
.step p{font-size:14.5px;line-height:25px;margin-top:6px;color:#333}

/* categories */
.categories{top:1220px;height:662px;background:var(--grey-band)}
.cat{position:absolute;width:241px;height:219px;background:#fff;border-radius:6px}
.cat .icon{position:absolute;left:22px;top:26px;width:77px;height:77px;background:var(--pale);border-radius:6px;display:flex;align-items:center;justify-content:center}
.cat h3{position:absolute;left:22px;top:130px;font-size:22px;font-weight:600}
.cat p{position:absolute;left:22px;top:176px;font-size:13px;color:var(--navy);font-weight:500;display:flex;align-items:center;gap:5px}
.cat.featured{background:var(--navy)}
.cat.featured h3,.cat.featured p{color:#fff}
.cat.featured .icon{background:#2457aa}

/* about */
.about{top:1882px;height:589px;background:#fff}
.about-band{left:705px;top:0;width:495px;height:589px;background:var(--pale)}
.about-photo{left:615px;top:66px;width:512px;height:457px;border-radius:4px;background:linear-gradient(160deg,#8a9a6e 0%,#c9c24a 40%,#5d6b45 70%,#39412f 100%)}
.about h2{position:absolute;left:75px;top:96px;font-size:40px;line-height:46px}
.about p{position:absolute;left:75px;top:206px;width:515px;font-size:14.5px;line-height:30.6px}
.btn-solid{position:absolute;left:75px;top:422px;width:177px;height:60px;background:var(--navy);color:#fff;border-radius:6px;font-weight:600;font-size:16px;display:flex;align-items:center;justify-content:center}

/* latest jobs */
.jobs{top:2471px;height:604px;background:linear-gradient(120deg,#0e3f94,#0b3a8d 60%,#0d449b)}
.tabs{position:absolute;left:75px;top:74px;display:flex;gap:32px;font-size:13.5px;color:#fff;font-weight:500}
.tabs .on{border-bottom:2px solid #fff;padding-bottom:3px;font-weight:600}
.jobs .section-title{color:#fff;top:62px}
.arrows{position:absolute;display:flex;gap:14px}
.arrow{width:32px;height:32px;border-radius:50%;display:flex;align-items:center;justify-content:center}
.job{position:absolute;top:138px;width:328px;height:275px;background:#fff;border-radius:6px}
.job h3{position:absolute;left:22px;top:26px;font-size:22px;font-weight:600}
.job .meta{position:absolute;left:22px;top:76px;display:flex;gap:14px;font-size:13px;color:var(--navy);font-weight:500}
.job .meta span{display:flex;align-items:center;gap:4px}
.job p{position:absolute;left:22px;top:108px;width:285px;font-size:14.5px;line-height:26px}
.btn-outline{position:absolute;border:2px solid var(--navy);color:var(--navy);border-radius:6px;font-weight:600;font-size:14px;display:flex;align-items:center;justify-content:center}
.jobs-more{left:510px;top:473px;width:178px;height:60px;border:2px solid #fff;border-radius:6px;color:#fff;font-weight:600;font-size:16px;display:flex;align-items:center;justify-content:center}

/* testimonials */
.testimonials{top:3075px;height:504px}
.quote-card{position:absolute;top:149px;width:330px;height:277px;background:#fff;border-radius:6px;box-shadow:0 0 14px rgba(0,0,0,.13)}
.quote-mark{position:absolute;left:20px;top:8px;font-size:80px;line-height:1;color:#b8c9e6;font-weight:700;font-family:Georgia,serif}
.quote-card p{position:absolute;left:22px;top:40px;width:290px;font-size:14.5px;line-height:25.7px}
.avatar{position:absolute;left:22px;top:182px;width:70px;height:70px;border-radius:50%;background:linear-gradient(135deg,#e6b54a,#7a5a3a 60%,#3c3c44)}
.quote-card .name{position:absolute;left:112px;top:205px;font-size:17px;color:var(--navy);font-weight:500}

/* news */
.news{top:3579px;height:533px;background:var(--grey-band)}
.news h2{position:absolute;left:75px;top:66px;font-size:33px}
.news-card{position:absolute;top:146px;width:512px;height:318px;overflow:hidden}
.news-card .photo{position:absolute;inset:0}
.news-card .date{position:absolute;left:22px;top:210px;font-size:14px;color:#fff}
.news-card h3{position:absolute;left:22px;top:232px;width:470px;font-size:21px;line-height:30px;color:#fff;font-weight:700}

/* newsletter & footer */
.footer{top:4261px;height:551px;background:var(--footer)}
.newsletter{left:254px;top:4172px;width:692px;height:174px;background:linear-gradient(120deg,#0e3f94,#0b3a8d);border-radius:4px}
.newsletter h2{position:absolute;left:0;width:692px;top:26px;text-align:center;color:#fff;font-size:32px}
.newsletter .field{position:absolute;left:56px;top:89px;width:580px;height:49px;border:1px solid #9db2da;border-radius:5px}
.newsletter .field span{position:absolute;left:18px;top:14px;font-size:13px;color:#e6ecf7}
.newsletter .field b{position:absolute;right:8px;top:7px;width:36px;height:34px;background:#000;border-radius:5px;display:flex;align-items:center;justify-content:center}
.foot-brand{left:75px;top:4414px;font-size:30px;font-weight:700;color:#4d5568;line-height:1.1}
.foot-brand span{display:block;font-size:20px;letter-spacing:6px;padding-left:30px;font-weight:600;color:var(--navy)}
.foot-about{left:75px;top:4500px;width:250px;font-size:14px;line-height:26px;color:#e8e8e8}
.foot-col{top:4408px}
.foot-col h4{font-size:18px;color:#fff;font-weight:500;margin-bottom:14px}
.foot-col li{list-style:none;font-size:14px;color:#e8e8e8;line-height:34px}
.contact-row{display:flex;gap:18px;font-size:14px;color:#e8e8e8;line-height:26px;margin-bottom:10px}
.contact-row svg{flex:none;margin-top:6px}
.foot-rule{left:0;top:4663px;width:1200px;height:1px;background:#3a3b3e}
.copyright{left:0;width:1200px;top:4705px;text-align:center;font-size:14px;color:#e8e8e8}
.social{left:0;width:1200px;top:4744px;display:flex;justify-content:center;gap:16px}
.social i{width:28px;height:28px;border-radius:50%;background:#fff;display:block}
</style>
</head>
<body>

<header class="section site-header">
  <div class="abs brand">Brightmoor<span>Talent</span></div>
  <div class="abs nav active" style="left:411px">Home</div>
  <div class="abs nav" style="left:490px">Categories</div>
  <div class="abs nav" style="left:611px">About Us</div>
  <div class="abs nav" style="left:714px">Jobs</div>
  <div class="abs nav" style="left:784px">Latest News</div>
  <div class="abs nav" style="left:910px">Contact Us</div>
  <div class="abs login">Log in
    <svg width="14" height="14" viewBox="0 0 14 14"><path d="M2 7h9M7 3l4 4-4 4" stroke="#fff" stroke-width="2" fill="none"/></svg>
  </div>
</header>

<section class="section hero">
  <div class="abs hero-photo" role="img" aria-label="Smiling tradesman in blue overalls and yellow hard hat giving a thumbs up beside industrial pipework"></div>
  <h1>Find The Job That<br>Fits Your Life</h1>
  <p>Skilled trade roles across Australia for qualified workers from Sri Lanka. We guide your visa path so you can focus on the work.</p>
  <div class="abs search"><span>Enter Keyword</span><b>Search Jobs</b></div>
</section>

<section class="section steps">
  <h2 class="section-title" style="top:62px">Apply Just 3 Easy Step to</h2>
  <div class="step" style="left:76px">
    <div class="icon"><svg width="50" height="40" viewBox="0 0 50 40"><rect x="7" y="3" width="36" height="25" rx="2" fill="none" stroke="#0b3d91" stroke-width="4"/><rect x="2" y="31" width="46" height="5" rx="2" fill="#0b3d91"/></svg></div>
    <h3>Account</h3>
    <p>Register in minutes and tell us your trade, licences and preferred Australian state.</p>
  </div>
  <div class="step" style="left:345px">
    <div class="icon"><svg width="34" height="44" viewBox="0 0 34 44"><path d="M2 2h20l10 10v30H2z" fill="#0b3d91"/><path d="M9 20h16M9 27h16M9 34h16" stroke="#fff" stroke-width="2.5"/></svg></div>
    <h3>CV/Resume</h3>
    <p>Upload your CV and trade papers. We check them against Australian standards.</p>
  </div>
  <div class="step" style="left:615px">
    <div class="icon"><svg width="48" height="40" viewBox="0 0 48 40"><rect x="16" y="2" width="16" height="8" rx="2" fill="none" stroke="#0b3d91" stroke-width="3"/><rect x="2" y="9" width="44" height="29" rx="4" fill="#0b3d91"/><path d="M12 9v29M36 9v29" stroke="#dcecf8" stroke-width="2"/></svg></div>
    <h3>Quick Jobs</h3>
    <p>Browse verified openings from Australian employers ready to sponsor you.</p>
  </div>
  <div class="step" style="left:884px">
    <div class="icon"><svg width="46" height="44" viewBox="0 0 46 44"><rect x="2" y="18" width="9" height="24" fill="#0b3d91"/><path d="M14 20 24 4c4 0 5 3 4 7l-2 6h14c3 0 5 3 4 6l-4 16c-1 2-2 3-4 3H14z" fill="#0b3d91"/></svg></div>
    <h3>Apply Them</h3>
    <p>Apply in one click and we guide you through interviews, visas and relocation.</p>
  </div>
</section>

<section class="section categories">
  <h2 class="section-title" style="top:56px">Popular Job Categories</h2>
  <div class="cat" style="left:75px;top:135px"><div class="icon"><svg width="42" height="42" viewBox="0 0 42 42" fill="none" stroke="#0b3d91" stroke-width="2"><circle cx="21" cy="16" r="12"/><path d="M14 16h14M21 9v14"/><path d="M10 40c0-6 5-10 11-10s11 4 11 10"/></svg></div><h3>Aged Care</h3><p><svg width="12" height="11"><rect y="2" width="12" height="9" fill="#0b3d91"/></svg>84 Job Vacancy</p></div>
  <div class="cat" style="left:346px;top:135px"><div class="icon"><svg width="42" height="42" viewBox="0 0 42 42" fill="none" stroke="#0b3d91" stroke-width="2"><path d="M10 16a11 11 0 0 1 22 0z"/><path d="M8 16h26"/><circle cx="21" cy="22" r="5"/><path d="M6 40c0-8 7-12 15-12s15 4 15 12"/></svg></div><h3>Construction</h3><p><svg width="12" height="11"><rect y="2" width="12" height="9" fill="#0b3d91"/></svg>126 Job Vacancy</p></div>
  <div class="cat featured" style="left:617px;top:135px"><div class="icon"><svg width="42" height="42" viewBox="0 0 42 42" fill="none" stroke="#fff" stroke-width="2.2"><path d="M8 34 26 16M24 8a7 7 0 0 1 10 10l-4-1-1-4z"/><path d="M10 8l6 6M8 10l4-4M24 26l10 10"/></svg></div><h3>Mechanical</h3><p><svg width="12" height="11"><rect y="2" width="12" height="9" fill="#fff"/></svg>100 Job Vacancy</p></div>
  <div class="cat" style="left:884px;top:135px"><div class="icon"><svg width="42" height="42" viewBox="0 0 42 42" fill="none" stroke="#0b3d91" stroke-width="2"><path d="M12 14a9 9 0 0 1 18 0z"/><circle cx="21" cy="20" r="6"/><path d="M8 40c0-7 6-11 13-11s13 4 13 11"/><rect x="24" y="30" width="10" height="8"/></svg></div><h3>Welding</h3><p><svg width="12" height="11"><rect y="2" width="12" height="9" fill="#0b3d91"/></svg>72 Job Vacancy</p></div>
  <div class="cat" style="left:75px;top:376px"><div class="icon"><svg width="42" height="42" viewBox="0 0 42 42" fill="none" stroke="#0b3d91" stroke-width="2"><rect x="8" y="4" width="26" height="34" rx="2"/><circle cx="21" cy="18" r="6"/><path d="M14 32h14"/></svg></div><h3>Electrical</h3><p><svg width="12" height="11"><rect y="2" width="12" height="9" fill="#0b3d91"/></svg>95 Job Vacancy</p></div>
  <div class="cat" style="left:346px;top:376px"><div class="icon"><svg width="42" height="42" viewBox="0 0 42 42" fill="none" stroke="#0b3d91" stroke-width="2"><circle cx="20" cy="7" r="4"/><path d="M20 12l-4 12 6 6-2 10M16 24l-8 14M20 14l10 6M28 8l8 8"/></svg></div><h3>Mining</h3><p><svg width="12" height="11"><rect y="2" width="12" height="9" fill="#0b3d91"/></svg>58 Job Vacancy</p></div>
  <div class="cat" style="left:617px;top:376px"><div class="icon"><svg width="42" height="42" viewBox="0 0 42 42" fill="none" stroke="#0b3d91" stroke-width="2"><circle cx="21" cy="21" r="9"/><path d="M21 4v6M21 32v6M4 21h6M32 21h6M9 9l4 4M29 29l4 4M9 33l4-4M29 13l4-4"/></svg></div><h3>Manufacturing</h3><p><svg width="12" height="11"><rect y="2" width="12" height="9" fill="#0b3d91"/></svg>110 Job Vacancy</p></div>
  <div class="cat" style="left:884px;top:376px"><div class="icon"><svg width="42" height="42" viewBox="0 0 42 42" fill="none" stroke="#0b3d91" stroke-width="2"><rect x="6" y="16" width="14" height="22"/><path d="M10 22h6M10 28h6M24 6l10 10M30 4l6 6-4 4-6-6zM26 18l-4 4"/></svg></div><h3>Carpentry</h3><p><svg width="12" height="11"><rect y="2" width="12" height="9" fill="#0b3d91"/></svg>67 Job Vacancy</p></div>
</section>

<section class="section about">
  <div class="abs about-band"></div>
  <div class="abs about-photo" role="img" aria-label="Three smiling workers in yellow hard hats and high-visibility vests standing with arms crossed"></div>
  <h2>About<br>Brightmoor Talent</h2>
  <p>Brightmoor Talent connects skilled tradespeople from Sri Lanka with employers across Australia. We place electricians, welders, fitters and builders into long-term roles, and we manage skills assessment, visa sponsorship and arrival support. Every candidate is screened in Colombo and every employer is vetted in Australia, so both sides can hire with confidence.</p>
  <div class="btn-solid">Read More</div>
</section>

<section class="section jobs">
  <div class="tabs"><span class="on">Hot Jobs</span><span>Recent Jobs</span><span>Popular Jobs</span></div>
  <h2 class="section-title">Latest Jobs Post</h2>
  <div class="arrows" style="left:1047px;top:66px">
    <div class="arrow" style="background:#fff"><svg width="16" height="16" viewBox="0 0 16 16"><path d="M13 8H3M7 4 3 8l4 4" stroke="#0b3d91" stroke-width="2.4" fill="none"/></svg></div>
    <div class="arrow" style="background:#fff"><svg width="16" height="16" viewBox="0 0 16 16"><path d="M3 8h10M9 4l4 4-4 4" stroke="#0b3d91" stroke-width="2.4" fill="none"/></svg></div>
  </div>
  <div class="job" style="left:75px"><h3>Electrician</h3><div class="meta"><span><svg width="10" height="13" viewBox="0 0 10 13"><path d="M5 0a5 5 0 0 1 5 5c0 4-5 8-5 8S0 9 0 5a5 5 0 0 1 5-5z" fill="#222"/></svg>Perth</span><span><svg width="13" height="11"><rect y="2" width="13" height="9" fill="#222"/></svg>Full Time</span><span><svg width="12" height="12"><circle cx="6" cy="3.5" r="3.2" fill="#222"/><path d="M0 12a6 5 0 0 1 12 0z" fill="#222"/></svg>3yrs Exp</span></div><p>Licensed electrician for commercial fit-outs. Visa sponsorship and relocation included.</p><div class="btn-outline" style="left:22px;top:202px;width:122px;height:42px">Apply Now</div></div>
  <div class="job" style="left:437px"><h3>Welder Fabricator</h3><div class="meta"><span><svg width="10" height="13" viewBox="0 0 10 13"><path d="M5 0a5 5 0 0 1 5 5c0 4-5 8-5 8S0 9 0 5a5 5 0 0 1 5-5z" fill="#222"/></svg>Brisbane</span><span><svg width="13" height="11"><rect y="2" width="13" height="9" fill="#222"/></svg>Full Time</span><span><svg width="12" height="12"><circle cx="6" cy="3.5" r="3.2" fill="#222"/><path d="M0 12a6 5 0 0 1 12 0z" fill="#222"/></svg>2yrs Exp</span></div><p>MIG and TIG welding on structural steel projects. Employer-sponsored four year role.</p><div class="btn-outline" style="left:22px;top:202px;width:122px;height:42px">Apply Now</div></div>
  <div class="job" style="left:798px"><h3>Diesel Mechanic</h3><div class="meta"><span><svg width="10" height="13" viewBox="0 0 10 13"><path d="M5 0a5 5 0 0 1 5 5c0 4-5 8-5 8S0 9 0 5a5 5 0 0 1 5-5z" fill="#222"/></svg>Adelaide</span><span><svg width="13" height="11"><rect y="2" width="13" height="9" fill="#222"/></svg>Full Time</span><span><svg width="12" height="12"><circle cx="6" cy="3.5" r="3.2" fill="#222"/><path d="M0 12a6 5 0 0 1 12 0z" fill="#222"/></svg>4yrs Exp</span></div><p>Service heavy vehicles for a regional fleet operator. Housing support on arrival.</p><div class="btn-outline" style="left:22px;top:202px;width:122px;height:42px">Apply Now</div></div>
  <div class="abs jobs-more">Read More</div>
</section>

<section class="section testimonials">
  <h2 class="section-title" style="top:61px">What Our Candidate Says</h2>
  <div class="arrows" style="left:1047px;top:66px">
    <div class="arrow" style="background:#6f7173"><svg width="16" height="16" viewBox="0 0 16 16"><path d="M13 8H3M7 4 3 8l4 4" stroke="#fff" stroke-width="2.4" fill="none"/></svg></div>
    <div class="arrow" style="background:var(--navy)"><svg width="16" height="16" viewBox="0 0 16 16"><path d="M3 8h10M9 4l4 4-4 4" stroke="#fff" stroke-width="2.4" fill="none"/></svg></div>
  </div>
  <div class="quote-card" style="left:73px"><div class="quote-mark">“</div><p>“ From my first call in Kandy to my first shift in Perth, the team handled every step. My skills assessment and visa were sorted in months, not years.”</p><div class="avatar" role="img" aria-label="Portrait of a candidate in a hard hat"></div><div class="name">Nuwan Perera</div></div>
  <div class="quote-card" style="left:435px"><div class="quote-mark">“</div><p>“ I was matched with a steel fabricator in Brisbane who valued my experience. The pre-departure briefing made moving my family so much easier.”</p><div class="avatar" role="img" aria-label="Portrait of a candidate in a yellow hard hat"></div><div class="name">Kasun Jayasena</div></div>
  <div class="quote-card" style="left:797px"><div class="quote-mark">“</div><p>“ Honest advice, clear fees and real jobs. Brightmoor Talent helped me turn twelve years as a mechanic into a secure career in Australia.”</p><div class="avatar" style="background:linear-gradient(135deg,#9aa3ad,#4b5260 60%,#2c2f36)" role="img" aria-label="Portrait of a candidate"></div><div class="name">Dilan Fernando</div></div>
</section>

<section class="section news">
  <h2>Latest News</h2>
  <div class="arrows" style="left:1047px;top:70px">
    <div class="arrow" style="background:#6f7173"><svg width="16" height="16" viewBox="0 0 16 16"><path d="M13 8H3M7 4 3 8l4 4" stroke="#fff" stroke-width="2.4" fill="none"/></svg></div>
    <div class="arrow" style="background:var(--navy)"><svg width="16" height="16" viewBox="0 0 16 16"><path d="M3 8h10M9 4l4 4-4 4" stroke="#fff" stroke-width="2.4" fill="none"/></svg></div>
  </div>
  <div class="news-card" style="left:75px">
    <div class="photo" role="img" aria-label="Two workers in hard hats inspecting machinery in a factory" style="background:linear-gradient(180deg,#6b7560 0%,#a69a52 40%,#3e3f3a 75%,#141414 100%)"></div>
    <div class="date">Nov,12, 2022</div>
    <h3>Australia expands skilled visa pathways for trade workers</h3>
  </div>
  <div class="news-card" style="left:615px">
    <div class="photo" role="img" aria-label="Woman in a high-visibility vest standing in a warehouse" style="background:linear-gradient(180deg,#6f6a5f 0%,#9c9a70 40%,#4a463c 75%,#151515 100%)"></div>
    <div class="date">Nov,12, 2022</div>
    <h3>How to prepare for your trade skills assessment</h3>
  </div>
</section>

<footer class="section footer"></footer>
<div class="abs newsletter">
  <h2>Newsletter Subscribe</h2>
  <div class="field"><span>Enter Email Address</span><b><svg width="16" height="16" viewBox="0 0 16 16"><path d="M1 8 15 1 11 15 8 9z" fill="#fff"/></svg></b></div>
</div>
<div class="abs foot-brand">Brightmoor<span>Talent</span></div>
<div class="abs foot-about">Connecting skilled Sri Lankan tradespeople with trusted employers across Australia.</div>
<div class="abs foot-col" style="left:364px"><h4>Job Categories</h4><ul><li>Construction</li><li>Electrical</li><li>Welding &amp; Fabrication</li><li>Mechanical</li><li>Aged Care</li></ul></div>
<div class="abs foot-col" style="left:634px"><h4>Resources</h4><ul><li>Visa Guide</li><li>Skills Assessment</li><li>Relocation Checklist</li><li>For Employers</li><li>FAQs</li></ul></div>
<div class="abs foot-col" style="left:886px"><h4>Contact Us</h4>
  <div class="contact-row"><svg width="14" height="12"><path d="M0 1l4-1 5 2 5-2v10l-5 2-5-2-4 1z" fill="#2a6fd6"/></svg><span>Level 4, 120 Harbour Street<br>Sydney NSW 2000</span></div>
  <div class="contact-row"><svg width="14" height="14" viewBox="0 0 14 14"><path d="M3 1l3 3-2 2c1 2 2 3 4 4l2-2 3 3-2 2C6 13 1 8 1 3z" fill="#2a6fd6"/></svg><span>+61 2 5550 1840</span></div>
  <div class="contact-row"><svg width="14" height="11"><rect width="14" height="11" rx="1" fill="#2a6fd6"/><path d="M0 1l7 5 7-5" stroke="#222325" fill="none"/></svg><span>hello@brightmoortalent.com</span></div>
</div>
<div class="abs foot-rule"></div>
<div class="abs copyright">Copyrights© 2022 Brightmoor Talent  All Rights Reserved</div>
<div class="abs social"><i></i><i></i><i></i><i></i><i></i></div>

</body>
</html>
```